Banner ads for LP that work with same theme as below banners

Love the banner ads below. Need more with attached photos. But use the same wording, font as in below banner ads. Should be LP size 1200/627 so I can use for Pixorly and LP. Looking for great ads to use as LP ads. We do lots of ads so it will be worth your time to enter this contest you will be rewarded with a ton of work. Need several banner ads that work together. So maybe 1 of the dresses, 1 of the sweater, 1 of the leggings, 1 of the jacket

Target Market(s)

Women 24-45

Industry/Entity Type

Fashion

Requirements
Must have
• Banner ads that work for LP and Pixorly
Nice to have
• Several options to choose from
Should not have
• not sure

```html
<!DOCTYPE html>
<html lang="en">
<head>
<meta charset="UTF-8">
<title>Our Best Dresses Ever – Banner</title>
<link href="https://fonts.googleapis.com/css2?family=Tinos:wght@700&family=Satisfy&display=swap" rel="stylesheet">
<style>
  :root {
    --bg-dark: #1c1c1c;
    --bg-mid: #262626;
    --bg-fold: #2e2e2e;
    --frame-edge: #c9c9c9;
    --frame-white: #ffffff;
    --photo-hair: #b27a45;
    --photo-dress: #2b2530;
    --photo-accent: #2c6fb8;
    --script-white: #ffffff;
    --headline-grey: #c8c2c2;
    --button-bg: #eeeeee;
    --button-text: #1a1a1a;
  }
  * { margin: 0; padding: 0; box-sizing: border-box; }
  html, body {
    width: 1200px;
    height: 627px;
    overflow: hidden;
    background: var(--bg-dark);
  }
  .banner {
    position: relative;
    width: 1200px;
    height: 627px;
    overflow: hidden;
    background: radial-gradient(ellipse at 70% 40%, var(--bg-mid) 0%, var(--bg-dark) 75%);
  }
  .banner__folds {
    position: absolute;
    inset: 0;
  }
  .photo-frame {
    position: absolute;
    left: 108px;
    top: 109px;
    width: 500px;
    height: 460px;
    transform: rotate(-8.6deg);
    background: var(--frame-white);
    border: 6px solid var(--frame-edge);
    padding: 10px;
    box-shadow: 0 6px 18px rgba(0,0,0,0.55);
  }
  .photo-frame__image {
    width: 100%;
    height: 100%;
    background:
      linear-gradient(180deg, transparent 0%, transparent 42%, var(--photo-dress) 60%),
      radial-gradient(ellipse at 35% 30%, var(--photo-hair) 0%, #d9b491 35%, #f4f0ee 70%),
      linear-gradient(90deg, var(--photo-dress), var(--photo-accent) 50%, var(--photo-dress));
  }
  .headline {
    position: absolute;
    left: 660px;
    top: 88px;
    width: 440px;
    text-align: center;
  }
  .headline__script {
    display: block;
    font-family: "Satisfy", cursive;
    font-size: 72px;
    line-height: 1;
    color: var(--script-white);
  }
  .headline__script--top { margin-left: -20px; }
  .headline__script--bottom { margin-top: 6px; margin-left: -30px; }
  .headline__word {
    display: block;
    margin-top: 2px;
    font-family: "Tinos", "Times New Roman", serif;
    font-weight: 700;
    font-size: 60px;
    line-height: 1;
    letter-spacing: 0.3em;
    margin-right: -0.3em;
    color: var(--headline-grey);
  }
  .cta {
    position: absolute;
    left: 719px;
    top: 376px;
    width: 319px;
    height: 58px;
    background: var(--button-bg);
    display: flex;
    align-items: center;
    justify-content: center;
    font-family: "Tinos", "Times New Roman", serif;
    font-weight: 700;
    font-size: 27px;
    color: var(--button-text);
    text-decoration: none;
  }
</style>
</head>
<body>
  <main class="banner">
    <svg class="banner__folds" width="1200" height="627" viewBox="0 0 1200 627" aria-hidden="true">
      <polygon points="0,0 1200,0 1200,40 0,20" fill="var(--bg-fold)" opacity="0.35"/>
      <polygon points="560,0 1200,0 1200,120" fill="var(--bg-fold)" opacity="0.25"/>
      <polygon points="900,627 1200,330 1200,627" fill="var(--bg-fold)" opacity="0.3"/>
      <line x1="860" y1="627" x2="1200" y2="300" stroke="#3a3a3a" stroke-width="1" opacity="0.6"/>
    </svg>

    <figure class="photo-frame">
      <div class="photo-frame__image" role="img" aria-label="Model with long wavy hair wearing a dark floral lace dress with blue flowers and bell sleeves"></div>
    </figure>

    <h1 class="headline">
      <span class="headline__script headline__script--top">Our Best</span>
      <span class="headline__word">DRESSES</span>
      <span class="headline__script headline__script--bottom">Ever!</span>
    </h1>

    <a class="cta" href="#">SHOP THE LOOK</a>
  </main>
</body>
</html>
```